Travel Agency Website - Simple General

Need a 7 page simple design that is pretty repetitive. Need to be able to load quickly that is SEO optimized. Trying to give ideas on what they can do, be personal as we are local, but at the same time come across as professional and get information easily with little burden.

- Landing Page
- Brimwell Vacations Page
- Family Trips
- Road Trips from Texas
- Other Destinations
- About Us Page
- Contact Us Page

Target Market(s)

Families

Coding

Coded - Design and coding required

Number of Pages Required

5+ page

Colors

Designer to choose colors to be used in the design.

Requirements
Must have
• Like it to flow easily with our logo. Use that for colors, etc.

```html
<!DOCTYPE html>
<html lang="en">
<head>
<meta charset="utf-8">
<title>Road Trips from Texas | Meander Lane Travel Co.</title>
<link rel="stylesheet" href="https://fonts.googleapis.com/css2?family=Poppins:wght@400;500;600;700&display=swap">
<style>
:root{
  --teal:#07495a;
  --gold:#b98333;
  --paper:#ebebe9;
  --white:#ffffff;
  --panel:#f8f8f8;
  --stripe:#e6ecee;
  --line:#d9dfe1;
  --rock:#9a5a45;
}
*{box-sizing:border-box;margin:0;padding:0}
html,body{width:752px;height:1200px;overflow:hidden;background:var(--white);font-family:'Poppins',sans-serif;color:var(--teal)}
.page{position:relative;width:752px;height:1200px;overflow:hidden}
.topbar{position:absolute;left:0;top:0;width:752px;height:39px;background:var(--paper)}
.topbar__phone{position:absolute;left:119px;top:12px;display:flex;align-items:center;gap:4px;font-size:10px;font-weight:600;color:var(--teal)}
.brand{position:absolute;left:349px;top:5px;width:54px;height:40px;display:flex;align-items:center;gap:3px;z-index:3}
.brand__dot{width:8px;height:8px;border-radius:50%;background:var(--gold);flex:none}
.brand__name{font-size:7px;font-weight:600;line-height:1.1;color:var(--teal)}
.social{position:absolute;top:13px;display:flex;gap:14px;right:120px}
.social span{width:11px;height:11px;border:1.5px solid var(--gold);border-radius:50%}
.nav{position:absolute;left:0;top:39px;width:752px;height:33px;background:var(--gold)}
.nav::before,.nav::after{content:"";position:absolute;left:0;right:0;border-top:1px dashed rgba(255,255,255,.8)}
.nav::before{top:4px}.nav::after{bottom:4px}
.nav ul{list-style:none;display:flex;justify-content:center;gap:20px;padding-top:12px;font-size:6.6px;color:var(--white);letter-spacing:.1px}
.hero{position:absolute;left:0;top:72px;width:752px;height:214px;background:linear-gradient(180deg,#6d3b2e 0%,var(--rock) 35%,#7a4a36 65%,#4d4a44 100%)}
.hero__title{position:absolute;left:0;right:0;top:94px;text-align:center;font-size:20px;font-weight:700;color:var(--white)}
.hero__edge{position:absolute;left:0;bottom:-1px;width:752px;height:34px}
.intro{position:absolute;left:0;right:0;top:325px;text-align:center}
.intro h1{font-size:20px;font-weight:700;line-height:1.3}
.intro p{font-size:6.5px;margin-top:4px}
.trips{position:absolute;left:128px;top:382px;width:495px;height:130px;border:1px solid var(--line);border-radius:12px;overflow:hidden;font-size:6.4px}
.trips__head{height:38px;background:var(--teal);color:var(--white);font-weight:700;font-size:8px;position:relative;border-radius:12px}
.trips__head span{position:absolute;top:14px}
.trips__row{position:relative}
.trips__row span{position:absolute}
.col-line{position:absolute;top:38px;bottom:0;border-left:1px solid var(--line)}
.inquiry{position:absolute;left:113px;top:543px;width:526px;height:492px;background:var(--panel);border-radius:12px}
.inquiry__title{position:absolute;left:15px;top:21px;width:496px;height:38px;background:var(--teal);border-radius:12px;color:var(--white);font-size:12px;font-weight:700;text-align:center;line-height:38px}
.field{position:absolute;left:20px;width:493px;height:32px;background:var(--white);border:1px solid var(--line);border-radius:6px;font-size:6.5px;padding:11px 11px;display:flex;justify-content:space-between}
.label{position:absolute;left:31px;font-size:6.5px;font-weight:600}
.submit{position:absolute;left:15px;top:440px;width:499px;height:39px;background:var(--gold);border-radius:14px;color:var(--white);font-size:12px;font-weight:700;text-align:center;line-height:39px}
.footer{position:absolute;left:0;top:1068px;width:752px;height:132px}
.footer__bg{position:absolute;inset:0}
.footer__brand{position:absolute;left:98px;top:36px;width:82px;height:76px;border-radius:50%;background:#eef3f0;display:flex;align-items:center;justify-content:center;gap:3px}
.footer__brand b{font-size:9px;font-weight:600;color:var(--teal);line-height:1.1}
.footer__info{position:absolute;left:277px;top:55px;display:flex;align-items:center;color:var(--white);font-size:6.8px;gap:8px}
.footer__sep{width:1px;height:14px;background:rgba(255,255,255,.3);margin:0 8px}
.footer__social{position:absolute;left:636px;top:55px;display:flex;gap:4px}
.footer__social span{width:11px;height:11px;border-radius:50%;background:var(--gold)}
.footer__rule{position:absolute;left:271px;top:79px;width:399px;border-top:1px solid rgba(255,255,255,.25)}
.footer__legal{position:absolute;left:277px;top:88px;width:393px;display:flex;justify-content:space-between;color:var(--white);font-size:6.5px}
</style>
</head>
<body>
<div class="page">
  <header>
    <div class="topbar">
      <div class="topbar__phone">
        <svg width="10" height="10" viewBox="0 0 24 24"><path fill="#b98333" d="M6.6 10.8a15 15 0 0 0 6.6 6.6l2.2-2.2c.3-.3.7-.4 1-.2 1.1.4 2.3.6 3.6.6.6 0 1 .4 1 1V20c0 .6-.4 1-1 1C10.6 21 3 13.4 3 4c0-.6.4-1 1-1h3.5c.6 0 1 .4 1 1 0 1.3.2 2.5.6 3.6.1.3 0 .7-.2 1z"/></svg>
        111.111.1111
      </div>
      <div class="brand"><span class="brand__dot"></span><span class="brand__name">Meander Lane</span></div>
      <div class="social"><span></span><span></span></div>
    </div>
    <nav class="nav">
      <ul>
        <li>HOME</li><li>BRIMWELL VACATIONS</li><li>FAMILY TRIPS</li><li>TEXAS ROAD TRIPS</li><li>OTHER DESTINATIONS</li><li>ABOUT US</li><li>CONTACT</li>
      </ul>
    </nav>
  </header>

  <section class="hero" role="img" aria-label="Photo of a desert road winding through red rock canyon">
    <h2 class="hero__title">Road Trips from Texas</h2>
    <svg class="hero__edge" viewBox="0 0 752 34" preserveAspectRatio="none"><path fill="#fff" d="M0 14 L30 20 L70 16 L110 24 L160 18 L210 22 L250 12 L290 8 L330 12 L370 26 L420 20 L470 24 L520 18 L570 28 L610 22 L650 16 L700 10 L752 14 L752 34 L0 34Z"/></svg>
  </section>

  <section class="intro">
    <h1>Explore Road Trip Options</h1>
    <p>In partnership with Piney Trail Van Rentals (Tyler, TX), we make your road trips easy, comfortable, and family-friendly.</p>
  </section>

  <div class="trips" role="table" aria-label="Road trip options">
    <div class="trips__head">
      <span style="left:16px">Trip Name</span>
      <span style="left:114px">Destination</span>
      <span style="left:217px">Duration</span>
      <span style="left:309px">Estimated Cost</span>
      <span style="left:427px">Best For</span>
    </div>
    <div class="trips__row" style="height:36px"><span style="left:16px;top:15px">Trip A</span><span style="left:93px;top:15px">Hill Country, TX</span><span style="left:214px;top:15px">3 Days</span><span style="left:323px;top:15px">Budget</span><span style="left:427px;top:15px">Families</span></div>
    <div class="trips__row" style="height:23px;background:var(--stripe)"><span style="left:16px;top:6px">Trip B</span><span style="left:93px;top:6px">Galveston Beach</span><span style="left:214px;top:6px">5 Days</span><span style="left:323px;top:6px">Moderate</span><span style="left:427px;top:7px">Family + Kids</span></div>
    <div class="trips__row" style="height:33px"><span style="left:16px;top:12px">Trip C</span><span style="left:93px;top:12px">Big Bend National Park</span><span style="left:214px;top:12px">4 Days</span><span style="left:323px;top:12px">Luxury</span><span style="left:427px;top:12px">Adventure Lovers</span></div>
    <i class="col-line" style="left:65px"></i><i class="col-line" style="left:171px"></i><i class="col-line" style="left:285px"></i><i class="col-line" style="left:400px"></i>
  </div>

  <form class="inquiry">
    <h2 class="inquiry__title">Road Trip Inquiry Form</h2>
    <div class="field" style="top:72px"><span>Which Trip Are You Interested in?</span><span>⌄</span></div>
    <div class="field" style="top:112px"><span>How Many People in Your Party?</span></div>
    <div class="field" style="top:151px"><span>Do You Need a Van Rental?</span></div>
    <div class="label" style="top:190px">Start Date</div>
    <div class="field" style="top:200px"><span>mm/dd/yyyy</span><span>▭</span></div>
    <div class="label" style="top:238px">End Date</div>
    <div class="field" style="top:248px"><span>mm/dd/yyyy</span><span>▭</span></div>
    <div class="field" style="top:288px"><span>What Kind of Trip?</span><span>⌄</span></div>
    <div class="field" style="top:328px;height:102px"><span>Any additional notes</span></div>
    <div class="submit">Submit Trip Request</div>
  </form>

  <footer class="footer">
    <svg class="footer__bg" viewBox="0 0 752 132" preserveAspectRatio="none"><path fill="#07495a" d="M0 22 L40 20 L90 10 L140 14 L200 6 L260 16 L320 22 L380 12 L440 10 L500 14 L560 8 L620 12 L670 2 L710 8 L752 4 L752 132 L0 132Z"/></svg>
    <div class="footer__brand"><span class="brand__dot"></span><b>Meander<br>Lane</b></div>
    <div class="footer__info">
      <span>☎ 111.111.1111</span><span class="footer__sep"></span><span>✉ hello@meanderlanetravel.com</span>
    </div>
    <div class="footer__social"><span></span><span></span></div>
    <div class="footer__rule"></div>
    <div class="footer__legal"><span>2026 Meander Lane Travel Co. All Right Reserved</span><span>Terms &amp; &nbsp;|&nbsp; Conditions &nbsp;|&nbsp; Privacy Policy</span></div>
  </footer>
</div>
</body>
</html>
```